Tri fold Brochure for a therapy center that specializes in divorcing families

I need to have a trifold brochure designed. The formatting is off so, I would need someone to reformat it. I would also like to make tweaks to the design and would welcome any design advice. This brochure is for a legal/therapuetic program called the Lantern Course. Here's a link to my website so you can get the feel. https://www.tidewell-harbor.example. I don't want a dark background. I would like dark colors to be accent colors. If you can make the bridge design nicer, that would be great.

Target Market(s)

attorneys, people divorcing or separating,, mediators

Industry/Entity Type

therapy and law

Font styles to use
Other font styles liked:
• Try to match it to the LC Brochure attached

Requirements
Must have
• I would like the colors to match m y website, using blues more as an accent rather than the major color. https://www.tidewell-harbor.examplehttps://www.tidewell-harbor.exampleI need to add my business logo
Nice to have
• I need to add my QR code as well and logo

```html
<!DOCTYPE html>
<html lang="en">
<head>
<meta charset="utf-8">
<title>Lantern Course Brochure – Back</title>
<link href="https://fonts.googleapis.com/css2?family=Noto+Serif:wght@400;500&family=Fira+Sans:ital,wght@0,400;0,500;0,600;1,400;1,600&display=swap" rel="stylesheet">
<style>
:root{
  --navy:#0f1d4f;
  --navy-deep:#0c1a49;
  --gold:#c99a34;
  --gold-soft:#d9b46a;
  --cream:#fcf3e6;
  --cream-line:#f1d4a8;
  --stage:#b3b3b3;
  --paper:#ffffff;
}
*{margin:0;padding:0;box-sizing:border-box}
html,body{width:1200px;height:893px;overflow:hidden;background:var(--stage)}
body{position:relative;font-family:"Fira Sans",sans-serif;color:var(--navy)}
.abs{position:absolute}
.side-label{left:0;width:1200px;top:24px;text-align:center;font-family:"Noto Serif",serif;font-size:33px;color:#fff;letter-spacing:1px}
.sheet{left:72px;top:84px;width:1056px;height:747px;background:var(--paper);overflow:hidden}
.wave{position:absolute;left:0;top:0}
.serif{font-family:"Noto Serif",serif;font-weight:400;text-align:center;letter-spacing:1px}
.rule{height:1px;background:var(--gold)}
.rule-navy{height:1px;background:var(--navy)}
.dot{width:8px;height:8px;background:var(--gold);transform:rotate(45deg)}
/* left column */
.problems-title{left:104px;width:286px;top:126px;font-size:21px;line-height:22.5px}
.lead{left:104px;width:286px;top:233px;text-align:center;font-style:italic;font-size:14px}
.pill{left:104px;width:282px;height:38px;border-radius:19px;background:#fff;box-shadow:2px 3px 3px rgba(0,0,0,.12),0 0 0 1px #eef0f4 inset;display:flex;align-items:center}
.pill .badge{width:38px;height:38px;border-radius:50%;background:var(--navy);flex:none;display:flex;align-items:center;justify-content:center;color:#fff;font-weight:600;font-size:20px}
.pill span{margin-left:8px;font-size:12px;font-weight:500}
.missing{left:112px;top:566px;width:266px;height:171px;background:var(--cream);border:1px solid var(--cream-line);border-radius:12px}
.missing-inner{left:117px;top:571px;width:256px;height:161px;border:1px solid var(--cream-line);border-radius:9px}
.missing-badge{left:221px;top:540px;width:48px;height:48px;border-radius:50%;background:var(--navy);display:flex;align-items:center;justify-content:center}
.missing-title{left:112px;width:266px;top:595px;font-size:16.5px;line-height:17px}
.missing-text{left:130px;width:230px;top:652px;text-align:center;font-size:12px;line-height:15.7px;font-weight:500}
/* centre column */
.hero-1{left:440px;width:320px;top:113px;font-size:27px;font-weight:500}
.hero-2{left:440px;width:320px;top:146px;font-size:19px}
.hero-3{left:440px;width:320px;top:170px;font-size:33px;line-height:29px;font-weight:500}
.promise{left:465px;top:264px;width:271px;height:79px;background:var(--cream);border:1px solid var(--cream-line);border-radius:3px;display:flex;align-items:center;justify-content:center;text-align:center;font-style:italic;font-weight:600;font-size:14.3px;line-height:21.5px}
.bridge-art{left:443px;top:372px;width:316px;height:116px;border-radius:4px;background:linear-gradient(180deg,#e7ecf6 0%,#f6ecd8 100%)}
.art-label{top:492px;font-family:"Noto Serif",serif;font-size:9.5px;text-align:center;width:120px}
.ribbon-end{top:506px;width:40px;height:22px;background:var(--gold)}
.ribbon{left:476px;top:511px;width:248px;height:27px;background:var(--navy);color:#fff;font-weight:600;font-size:20px;letter-spacing:1px;display:flex;align-items:center;justify-content:center}
.pillars{left:440px;width:320px;top:543px;text-align:center;font-size:12px;font-weight:500}
.why{left:440px;width:320px;top:569px;text-align:center;font-size:12.5px;font-weight:600}
.benefit{width:87px;height:85px;background:#fff;box-shadow:1px 2px 3px rgba(0,0,0,.15),0 0 0 1px #eef0f4 inset;text-align:center;font-size:9.5px;font-weight:500;line-height:12px;padding-top:7px}
.benefit i{display:block;width:28px;height:28px;margin:0 auto 5px;border-radius:50%;background:var(--gold)}
/* right column */
.service{left:816px;width:272px;background:#fff;border:2px solid var(--navy);border-radius:13px;overflow:hidden}
.service.legal{border-color:var(--gold)}
.service-head{height:58px;background:var(--navy);color:#fff;font-family:"Noto Serif",serif;font-size:18px;text-align:center;padding-top:31px;letter-spacing:.5px}
.legal .service-head{background:var(--gold)}
.service ul{list-style:none;padding:0 26px}
.service li{display:flex;align-items:center;height:40px;font-size:15px;border-bottom:1px solid var(--navy)}
.legal li{border-bottom-color:var(--gold);height:38px}
.service li:last-child{border-bottom:none}
.service li b{width:18px;height:18px;border-radius:50%;background:var(--navy);margin:0 14px 0 2px;flex:none}
.legal li b{background:var(--gold)}
.seal{width:46px;height:46px;border-radius:50%;border:2px solid #fff;outline:2px solid var(--navy)}
.seal.navy{background:var(--navy)}
.seal.gold{background:var(--gold);outline-color:var(--gold)}
.closing{left:840px;width:230px;text-align:center;font-size:12px;line-height:15.5px}
</style>
</head>
<body>
<div class="abs side-label">BACK</div>

<div class="abs sheet">
  <svg class="wave" width="1056" height="747" viewBox="0 0 1056 747" aria-hidden="true">
    <path d="M0 670 Q528 738 1056 718 L1056 747 L0 747Z" fill="#c99a34"/>
    <path d="M0 684 Q528 748 1056 725 L1056 747 L0 747Z" fill="#0c1a49"/>
  </svg>
</div>

<!-- Left panel -->
<h2 class="abs serif problems-title">FAMILIES OFTEN<br>FEEL STUCK<br>BETWEEN TWO SYSTEMS</h2>
<div class="abs rule" style="left:122px;top:211px;width:120px"></div>
<div class="abs dot" style="left:250px;top:207px"></div>
<div class="abs rule" style="left:265px;top:211px;width:108px"></div>
<p class="abs lead">The Lantern Course helps Alleviate:</p>

<div class="abs pill" style="top:263px"><div class="badge">
  <svg width="22" height="22" viewBox="0 0 22 22" fill="none" stroke="#fff" stroke-width="1.6"><ellipse cx="11" cy="11" rx="9" ry="4"/><ellipse cx="11" cy="11" rx="9" ry="4" transform="rotate(60 11 11)"/><ellipse cx="11" cy="11" rx="9" ry="4" transform="rotate(120 11 11)"/></svg>
</div><span>Stress and Uncertainty</span></div>
<div class="abs pill" style="top:308px"><div class="badge">
  <svg width="22" height="20" viewBox="0 0 22 20"><rect x="1" y="1" width="20" height="14" rx="3" fill="#fff"/><path d="M5 15 L4 19 L9 15Z" fill="#fff"/><circle cx="7" cy="8" r="1.5" fill="#0f1d4f"/><circle cx="11" cy="8" r="1.5" fill="#0f1d4f"/><circle cx="15" cy="8" r="1.5" fill="#0f1d4f"/></svg>
</div><span>Communication Problems</span></div>
<div class="abs pill" style="top:353px"><div class="badge"></div><span>Children Caught in the Middle</span></div>
<div class="abs pill" style="top:398px"><div class="badge">
  <svg width="20" height="22" viewBox="0 0 20 22" fill="#fff"><rect x="9" y="1" width="2.5" height="20"/><path d="M3 5 H17 L19 7.5 L17 10 H3Z"/><path d="M17 12 H3 L1 14.5 L3 17 H17Z"/></svg>
</div><span>Conflicting Guidance From professionals</span></div>
<div class="abs pill" style="top:443px"><div class="badge">
  <svg width="24" height="24" viewBox="0 0 24 24" fill="none" stroke="#fff" stroke-width="2"><path d="M12 2v3M12 19v3M2 12h3M19 12h3M12 8v5l4 3"/></svg>
</div><span>Conflicting Therapeutic and Legal Timelines</span></div>
<div class="abs pill" style="top:488px"><div class="badge">$</div><span>Mounting Legal Fees</span></div>

<div class="abs missing"></div>
<div class="abs missing-inner"></div>
<div class="abs missing-badge"><div style="width:22px;height:22px;background:var(--gold);border-radius:3px"></div></div>
<h3 class="abs serif missing-title">THE MISSING PIECE OF<br>COORDINATED CARE</h3>
<div class="abs rule" style="left:147px;top:639px;width:90px"></div>
<div class="abs dot" style="left:246px;top:635px"></div>
<div class="abs rule" style="left:261px;top:639px;width:83px"></div>
<p class="abs missing-text">Without coordination, families can feel overwhelmed, confused and stuck between two separate systems</p>

<!-- Centre panel -->
<h1 class="abs serif hero-1">BRIDGING THE GAP</h1>
<div class="abs rule" style="left:473px;top:157px;width:66px"></div>
<p class="abs serif hero-2">BETWEEN</p>
<div class="abs rule" style="left:658px;top:157px;width:66px"></div>
<h1 class="abs serif hero-3">THERAPEUTIC &amp;<br>LEGAL SYSTEMS</h1>
<div class="abs rule" style="left:469px;top:249px;width:117px"></div>
<div class="abs dot" style="left:596px;top:245px"></div>
<div class="abs rule" style="left:612px;top:249px;width:107px"></div>
<p class="abs promise">We provide coordinated wraparound<br>care so you can focus on yourself<br>and your family</p>

<div class="abs bridge-art" role="img" aria-label="Illustration of a navy and gold arched bridge joining two columns, with therapy and legal support emblems beneath"></div>
<p class="abs art-label" style="left:456px">THERAPY</p>
<p class="abs art-label" style="left:626px">LEGAL SUPPORT</p>

<div class="abs ribbon-end" style="left:451px;clip-path:polygon(0 0,100% 0,100% 100%,0 100%,35% 50%)"></div>
<div class="abs ribbon-end" style="left:709px;clip-path:polygon(0 0,100% 0,65% 50%,100% 100%,0 100%)"></div>
<div class="abs ribbon">COORDINATED CARE</div>
<p class="abs pillars">Communication &nbsp;•&nbsp; Collaboration &nbsp;•&nbsp; Consistency</p>
<div class="abs rule-navy" style="left:455px;top:577px;width:42px"></div>
<p class="abs why">WHY COORDINATED CARE MATTERS</p>
<div class="abs rule-navy" style="left:703px;top:577px;width:42px"></div>

<div class="abs benefit" style="left:458px;top:602px"><i></i>Keeps<br>Professionals<br>Aligned</div>
<div class="abs benefit" style="left:561px;top:602px"><i></i>Creates<br>Consistent<br>Expectations</div>
<div class="abs benefit" style="left:664px;top:602px"><i></i>Reduces<br>Confusion<br>and Conflict</div>
<div class="abs benefit" style="left:458px;top:700px"><i></i>Help Families<br>Focus on<br>Shared Goals</div>
<div class="abs benefit" style="left:561px;top:700px"><i></i>Supports<br>Healthier Family<br>Relationships</div>
<div class="abs benefit" style="left:664px;top:700px"><i></i>Promotes Better<br>Outcomes for<br>Children</div>

<!-- Right panel -->
<section class="abs service" style="top:130px;height:217px">
  <div class="service-head">THERAPY</div>
  <ul>
    <li><b></b>Family Therapy</li>
    <li><b></b>Individual Therapy</li>
    <li><b></b>Child Therapy</li>
    <li><b></b>Parent Support</li>
  </ul>
</section>
<div class="abs seal navy" style="left:928px;top:111px"></div>

<section class="abs service legal" style="top:387px;height:173px">
  <div class="service-head">LEGAL SUPPORT</div>
  <ul>
    <li><b></b>Guardian Ad Litem</li>
    <li><b></b>Evaluate Mediator</li>
    <li><b></b>Parent Support</li>
  </ul>
</section>
<div class="abs seal gold" style="left:928px;top:367px"></div>

<div class="abs rule" style="left:820px;top:585px;width:122px"></div>
<div class="abs dot" style="left:947px;top:581px"></div>
<div class="abs rule" style="left:962px;top:585px;width:121px"></div>
<div class="abs" style="left:934px;top:611px;width:40px;height:40px;border-radius:50%;background:var(--navy)"></div>
<p class="abs closing" style="top:657px">The Lantern Course bridges the gap between legal and therapeutic Support for divorcing and seperating families</p>
<div class="abs rule" style="left:871px;top:724px;width:70px"></div>
<div class="abs dot" style="left:947px;top:720px"></div>
<div class="abs rule" style="left:962px;top:724px;width:70px"></div>
<p class="abs closing" style="top:741px">The Lantern Course bridges the gap between legal and therapeutic Support for divorcing and seperating families</p>
</body>
</html>
```